Lumen Fitness Personal Training Business

I need a business card design with a logo for my personal training company. I'd like the colors to be a vibrant green and black. I'd like the logo to incorporate an anvil (or something similar). I train hardcore competitive athletes as well as soccer moms trying to get and/or stay in shape. I need a logo that will not pigeon hole me in one category or the other, but at the same time not be too intimidating to soccer moms, but will not be off putting to the more hardcore trainees. The design should be attention grabbing and aesthetic.
Target Market(s)
Hardcore athletes as well as average people just trying to get/stay in shape.
Industry/Entity Type
Training

```html
<!DOCTYPE html>
<html lang="en">
<head>
<meta charset="utf-8">
<title>Lumen Fitness – Business Card</title>
<link href="https://fonts.googleapis.com/css2?family=Lato:wght@400;700;900&display=swap" rel="stylesheet">
<style>
  :root {
    --backdrop: #2a2522;
    --card: #1c1c1c;
    --card-back: #161616;
    --green: #3dbb4a;
    --white: #f2f2f2;
    --silver: #9a9a9a;
    --divider: #2e2e2e;
  }
  * { box-sizing: border-box; margin: 0; padding: 0; }
  html, body {
    width: 1200px;
    height: 844px;
    overflow: hidden;
    background: var(--backdrop);
    font-family: "Lato", sans-serif;
  }
  .stage {
    width: 1200px;
    height: 844px;
    display: flex;
    align-items: center;
    justify-content: center;
    gap: 40px;
  }
  .card {
    width: 540px;
    height: 309px;
    border-radius: 4px;
    overflow: hidden;
    display: flex;
  }
  .card--front { background: var(--card); }
  .card--back {
    background: var(--card-back);
    align-items: center;
    justify-content: center;
  }
  .brand {
    display: flex;
    flex-direction: column;
    align-items: center;
    justify-content: center;
    gap: 16px;
  }
  .brand--front {
    width: 290px;
    flex-shrink: 0;
    padding: 0 26px;
  }
  .brand__mark {
    width: 64px;
    height: 64px;
    background: var(--green);
  }
  .brand__name {
    font-weight: 900;
    font-size: 26px;
    letter-spacing: 0.5px;
    color: var(--green);
    text-transform: uppercase;
    white-space: nowrap;
    line-height: 1;
  }
  .brand--back .brand__mark {
    width: 84px;
    height: 84px;
    background: var(--silver);
  }
  .brand--back .brand__name {
    color: var(--silver);
    font-size: 34px;
  }
  .divider {
    width: 1px;
    margin: 62px 0;
    background: var(--divider);
    flex-shrink: 0;
  }
  .contact {
    padding: 58px 0 0 22px;
    display: flex;
    flex-direction: column;
    white-space: nowrap;
  }
  .contact__name {
    font-size: 21px;
    font-weight: 400;
    color: var(--green);
    line-height: 1.1;
  }
  .contact__role {
    font-size: 12.5px;
    color: var(--green);
    margin-bottom: 16px;
  }
  .contact__address {
    font-size: 13.5px;
    color: var(--white);
    line-height: 1.4;
    margin-bottom: 18px;
  }
  .contact__lines {
    list-style: none;
    font-size: 13.5px;
    color: var(--green);
    line-height: 1.45;
  }
</style>
</head>
<body>
  <main class="stage">
    <section class="card card--front" aria-label="Business card front">
      <div class="brand brand--front">
        <span class="brand__mark"></span>
        <span class="brand__name">Lumen Fitness</span>
      </div>
      <div class="divider"></div>
      <div class="contact">
        <h1 class="contact__name">Daniel Reyes</h1>
        <p class="contact__role">Managing Director</p>
        <p class="contact__address">48 Harbor Lane, Westfield<br>Northland, 204817.</p>
        <ul class="contact__lines">
          <li>T: 044-987 654 321</li>
          <li>E: hello@lumenfit.com</li>
          <li>W: www.lumenfit.com</li>
        </ul>
      </div>
    </section>

    <section class="card card--back" aria-label="Business card back">
      <div class="brand brand--back">
        <span class="brand__mark"></span>
        <span class="brand__name">Lumen Fitness</span>
      </div>
    </section>
  </main>
</body>
</html>
```